Website to design and sell sundials: www.gnomonvale.com

We have a website that creates a free paper sundial, we want to migrate from this not profit free website to a website where we will continue offering the free paper sundial model but We will also offer a manufactured sundial and sell it.
In order to understand the project, please visit:
http://www.gnomonvale.com/vertical/sundial.html and
http://www.torvel.net/landing/

The website user journey should be redesigned, including the phases that are,
select language
Show product give info
Creation/edit sundial (could be one or more phases)
View created sundial
Buy sundial.

May some of them could be combined or splitted, what It have more sense.

Requirements
Must have
• A description page user journey offering freemium paper sundial and physical sundial to sell.
• A sundial creation page for "free" paper sundial
• A result page for paper sundial
• A sell page for physical

```html
<!DOCTYPE html>
<html lang="en">
<head>
<meta charset="utf-8">
<title>GnomonVale.com – Sundials</title>
<link href="https://fonts.googleapis.com/css2?family=Raleway:wght@400;500;600;700&family=Open+Sans:wght@400;600&display=swap" rel="stylesheet">
<style>
:root{
  --red:#c4101c;
  --red-dark:#a00d17;
  --orange:#f8a93a;
  --orange-deep:#ef8f1c;
  --dark:#2a2b2d;
  --footer:#3b3b3b;
  --grey-bg:#efefef;
  --text:#333;
  --muted:#666;
  --white:#fff;
}
*{box-sizing:border-box;margin:0;padding:0}
html,body{width:1200px;height:2723px;overflow:hidden}
body{position:relative;background:var(--white);font-family:"Raleway",sans-serif;color:var(--text)}
.abs{position:absolute}

/* header */
.site-header{left:0;top:0;width:1200px;height:100px;background:var(--white);border-bottom:3px solid var(--red)}
.brand{left:100px;top:38px;display:flex;align-items:center;gap:14px;font-size:32px;font-weight:600;color:var(--red)}
.brand .dot{width:22px;height:22px;border-radius:50%;background:var(--orange)}
.main-nav{top:50px;left:0;width:1200px;font-size:16px;font-weight:500;color:#222}
.main-nav a{position:absolute;color:inherit;text-decoration:none;transform:translateX(-50%);white-space:nowrap}
.main-nav a.active{color:var(--red)}
.main-nav a.active::after{content:"";position:absolute;left:-14px;right:-14px;top:26px;height:8px;border-radius:50%;background:var(--red)}

/* hero */
.hero{left:0;top:103px;width:1200px;height:470px;background:linear-gradient(180deg,#c9d1d6 0%,#9aa8b0 35%,#5d7078 55%,#3f5058 80%,#6b6a62 100%)}
.hero-title{left:100px;top:258px;font-size:42px;font-weight:700;color:var(--red)}
.hero-sub{left:100px;top:334px;width:400px;font-size:21px;line-height:30px;color:#1f1f1f}
.hero-dots{left:100px;top:433px;display:flex;gap:9px}
.hero-dots span{width:14px;height:14px;border-radius:50%;border:2px solid var(--white)}
.hero-dots span.on{background:var(--red)}

/* intro */
.intro-band{left:0;top:500px;width:1200px;height:445px;background:radial-gradient(ellipse at 50% 15%,#fbb84e 0%,var(--orange) 50%,#f59e2c 100%)}
.section-title{left:0;width:1200px;text-align:center;font-family:"Open Sans",sans-serif;font-weight:600;font-size:35px;display:flex;justify-content:center;align-items:center;gap:16px}
.section-title .mark{width:18px;height:18px;border-radius:50%;background:currentColor}
.intro-title{top:634px;color:var(--white)}
.intro-text{left:345px;top:712px;width:700px;text-align:center;font-size:12.5px;line-height:22px;color:#fff6e8}
.feature{width:300px;text-align:center;transform:translateX(-50%)}
.feature .pic{width:190px;height:190px;border-radius:50%;margin:0 auto;border:3px solid #fde7c4;box-shadow:0 0 0 6px rgba(255,255,255,.25)}
.feature h3{margin-top:32px;font-size:18px;font-weight:600;color:#222}
.feature p{margin-top:12px;font-size:13px;line-height:20px;color:var(--muted)}

/* create */
.create-band{left:0;top:1165px;width:1200px;height:615px;background:linear-gradient(180deg,#3a3b3d,#1f2022 60%,#2d2e30)}
.create-title{top:1248px;color:var(--white)}
.create-text{left:200px;top:1316px;width:800px;text-align:center;font-size:13.5px;line-height:22px;color:#eee}
.globe{left:100px;top:1403px;width:236px;height:236px;border-radius:50%;border:4px solid var(--white);background:radial-gradient(circle at 40% 40%,#3f7ec0,#1f4c86 60%,#16345e)}
.badge{left:256px;top:1530px;width:152px;height:152px;border-radius:50%;background:var(--orange);border:4px solid var(--white);display:flex;align-items:center;justify-content:center;color:var(--white);font-size:17px;font-weight:600}
.create-copy{left:461px;top:1400px;width:600px;color:var(--white)}
.create-copy .cta{display:inline-block;font-size:24px;font-weight:600;padding-bottom:6px;border-bottom:2px solid var(--white)}
.create-copy h4{margin-top:22px;font-size:21px;font-weight:500}
.create-copy ol{list-style:none;margin-top:14px;font-size:14px;line-height:29px;color:#eee}
.btn-buy{display:inline-block;margin-top:14px;padding:11px 24px;background:var(--orange-deep);color:var(--white);font-size:18px;font-weight:500;border-radius:2px}

/* panels */
.panel{top:1800px;width:472px;height:255px;border:1px solid #ddd;background:var(--white)}
.panel-head{height:63px;display:flex;align-items:center;gap:16px;padding-left:20px;color:var(--white);font-size:25px;font-weight:500}
.panel-head .mark{width:16px;height:16px;border-radius:50%;background:var(--white)}
.panel.todo .panel-head{background:linear-gradient(180deg,#d41423,var(--red-dark))}
.panel.samples .panel-head{background:linear-gradient(180deg,#f9a838,var(--orange-deep))}
.panel-body{padding:22px 16px;font-size:14px;color:var(--text)}
.panel-body .lead{font-size:17px;margin-bottom:8px}
.panel-body ul{list-style:none;margin-top:14px}
.panel-body li{position:relative;padding-left:26px;font-size:13.5px;line-height:25px;color:#444}
.panel-body li::before{content:"";position:absolute;left:2px;top:7px;width:11px;height:11px;border-radius:50%;background:#222}
.panel-body li::after{content:"";position:absolute;left:5px;top:10px;width:4px;height:4px;border-top:1.5px solid #fff;border-right:1.5px solid #fff;transform:rotate(45deg)}

/* phases */
.phases-band{left:0;top:2087px;width:1200px;height:327px;background:var(--grey-bg)}
.phases-title{top:2104px;color:var(--red)}
.phase{top:2182px;height:192px;background:var(--white);padding:5px;border:1px solid #ddd}
.phase div{width:100%;height:100%;background:linear-gradient(135deg,#b5543a,#5a5c60 40%,#3d4043 60%,#b0513a)}

/* footer */
.site-footer{left:0;top:2414px;width:1200px;height:258px;background:var(--footer)}
.footer-brand{left:0;top:2460px;width:1200px;display:flex;justify-content:center;align-items:center;gap:12px;color:var(--white);font-size:26px;font-weight:500}
.footer-brand .dot{width:18px;height:18px;border-radius:50%;background:var(--white)}
.footer-nav{top:2553px;left:0;width:1200px;font-size:15px;color:var(--white)}
.footer-nav a{position:absolute;color:inherit;text-decoration:none;transform:translateX(-50%);white-space:nowrap}
.footer-nav .sep{position:absolute;top:0}
.social{top:2607px;width:40px;height:40px;border-radius:50%;border:2px solid var(--white)}
.copy-bar{left:0;top:2672px;width:1200px;height:51px;background:linear-gradient(180deg,#f7a33a,var(--orange-deep));text-align:center;line-height:51px;font-size:13px;color:#fff3e0}
</style>
</head>
<body>

<header class="abs site-header">
  <div class="abs brand"><span class="dot"></span>GnomonVale.com</div>
  <nav class="abs main-nav">
    <a class="active" style="left:666px" href="#">Introduction</a>
    <a style="left:799px" href="#">Create Sundial</a>
    <a style="left:930px" href="#">To Do List</a>
    <a style="left:1062px" href="#">Contact Us</a>
  </nav>
</header>

<section class="abs hero" role="img" aria-label="Photo of a bronze sundial on a stone wall overlooking the sea"></section>
<svg class="abs" style="left:0;top:480px" width="1200" height="110" aria-hidden="true">
  <path d="M0 60 Q600 140 1200 0 L1200 110 L0 110 Z" fill="#f8a93a"/>
</svg>
<h1 class="abs hero-title">GnomonVale.com</h1>
<p class="abs hero-sub">Sundials are instruments that tell you the time with the shadow of the sun.</p>
<div class="abs hero-dots"><span></span><span class="on"></span><span></span><span></span></div>

<section class="abs intro-band"></section>
<h2 class="abs section-title intro-title"><span class="mark"></span>Introduction</h2>
<p class="abs intro-text">This page is about Sundials. Sundials are instruments that tell you the time with the shadow of the sun. To design a sundial you need to know exactly where you are going to put it, i.e. you need to know the longitude, the latitude and the orientation of the wall with respect to North. I have designed this page and integrated MapGrid. It helps you to easily find all the parameters needed and finally produces a printable page with a cut-out paper sundial, that can be cut and folded to give you a vertical sundial.</p>

<div class="abs feature" style="left:254px;top:849px">
  <div class="pic" role="img" aria-label="Cut-out paper sundial fixed on a brick wall" style="background:linear-gradient(135deg,#a0573c,#d9dde2 45%,#9fb0bd 70%,#8c4a33)"></div>
  <h3>Cut Out Paper</h3>
  <p>Vertical Sundial customized to your place on earth and the declination of the wall you are going to put it on.</p>
</div>
<div class="abs feature" style="left:599px;top:849px">
  <div class="pic" role="img" aria-label="Paper sundial on a window seen from inside a room" style="background:linear-gradient(180deg,#6a5a4c,#cdb9a2 45%,#7a5a3c)"></div>
  <h3>Vertical Sundial</h3>
  <p>you have the possibility to put your vertical Sundial on a window and read the hour from inside the room.</p>
</div>
<div class="abs feature" style="left:940px;top:849px">
  <div class="pic" role="img" aria-label="Aerial view of buildings used to locate the wall" style="background:linear-gradient(135deg,#5f6d55,#a9aea4 50%,#4e5a48)"></div>
  <h3>Daylight-Saving Time</h3>
  <p>Your sundial can be configured to show civil time or civil daylight-saving time, so that it gives you.</p>
</div>
<svg class="abs" style="left:360px;top:860px" width="120" height="50" aria-hidden="true">
  <path d="M5 35 Q55 -5 108 30" stroke="#fff" stroke-width="5" fill="none" stroke-linecap="round"/>
  <path d="M92 22 L110 32 L100 46" stroke="#fff" stroke-width="5" fill="none" stroke-linecap="round"/>
</svg>
<svg class="abs" style="left:712px;top:975px" width="120" height="50" aria-hidden="true">
  <path d="M5 28 Q60 45 105 8" stroke="#f39a1e" stroke-width="5" fill="none" stroke-linecap="round"/>
  <path d="M88 6 L107 6 L106 25" stroke="#f39a1e" stroke-width="5" fill="none" stroke-linecap="round"/>
</svg>

<section class="abs create-band" role="img" aria-label="Dark photo of a sundial by the sea"></section>
<svg class="abs" style="left:0;top:1160px" width="1200" height="50" aria-hidden="true">
  <path d="M0 10 Q600 55 1200 10 L1200 0 L0 0 Z" fill="#fff"/>
</svg>
<svg class="abs" style="left:0;top:1730px" width="1200" height="52" aria-hidden="true">
  <path d="M0 52 L0 20 Q600 -15 1200 45 L1200 52 Z" fill="#fff"/>
</svg>
<h2 class="abs section-title create-title"><span class="mark"></span>Create Your Own Sundial</h2>
<p class="abs create-text">This page is about Sundials. Sundials are instruments that tell you the time with the shadow of the sun. To design a sundial you need to know exactly where you are going to put it, i.e. you need to know the longitude.</p>
<div class="abs globe" role="img" aria-label="Satellite globe of the Earth"></div>
<div class="abs badge">GnomonVale.com</div>
<div class="abs create-copy">
  <span class="cta">Click here to build your custom sundial!!!</span>
  <h4>Fill in the form and create your sundial</h4>
  <ol>
    <li>1. CALCULATE</li>
    <li>2. PRINT THE PDF. To print, please select "shrink to page" in order not to deform the shape .</li>
    <li>3. CUT AND FOLD: Once you have your model printed, you have to cut (RED LINES), and<br>fold (BLUE LINES)</li>
  </ol>
  <span class="btn-buy">Buy Sundial</span>
</div>

<section class="abs panel todo" style="left:100px">
  <div class="panel-head"><span class="mark"></span>To Do List</div>
  <div class="panel-body">
    <p class="lead">Consider this page beta, this is the TODO list.</p>
    <p>Where is the wall where you want to put your sundial on, located it with MapGrid.</p>
    <ul>
      <li>Check that all the latitudes are draw OK on the paper.</li>
      <li>Improve explanations and webpage design.</li>
    </ul>
  </div>
</section>
<section class="abs panel samples" style="left:628px">
  <div class="panel-head"><span class="mark"></span>Sundial Samples</div>
  <div class="panel-body">
    <p class="lead">Some sundial samples:</p>
    <ul>
      <li>South Hemisphere Buenos Aires</li>
      <li>Valencia South east</li>
      <li>Valencia NORTH WEST</li>
      <li>Valencia WEST</li>
    </ul>
  </div>
</section>

<section class="abs phases-band"></section>
<h2 class="abs section-title phases-title"><span class="mark"></span>Sundial Phases</h2>
<div class="abs phase" style="left:145px;width:278px"><div role="img" aria-label="Slate sundial on a brick wall, morning shadow"></div></div>
<div class="abs phase" style="left:465px;width:272px"><div role="img" aria-label="Slate sundial on a brick wall, midday shadow"></div></div>
<div class="abs phase" style="left:780px;width:280px"><div role="img" aria-label="Slate sundial on a brick wall, afternoon shadow"></div></div>

<footer class="abs site-footer"></footer>
<div class="abs footer-brand"><span class="dot"></span>GnomonVale.com</div>
<nav class="abs footer-nav">
  <a style="left:218px" href="#">Introduction</a>
  <span class="sep" style="left:304px">|</span>
  <a style="left:405px" href="#">Create Sundial</a>
  <span class="sep" style="left:512px">|</span>
  <a style="left:595px" href="#">To Do List</a>
  <span class="sep" style="left:678px">|</span>
  <a style="left:781px" href="#">Sundial Samples</a>
  <span class="sep" style="left:900px">|</span>
  <a style="left:986px" href="#">Contact Us</a>
</nav>
<span class="abs social" style="left:494px" aria-label="Social link"></span>
<span class="abs social" style="left:552px" aria-label="Social link"></span>
<span class="abs social" style="left:610px" aria-label="Social link"></span>
<span class="abs social" style="left:668px" aria-label="Social link"></span>
<div class="abs copy-bar">Copyrights 2016. GnomonVale. All rights reserved</div>

</body>
</html>
```